Road Construction Company needs business cards

We would like a new business card designed for our business.

We're a road construction company based in Qld, Australia.

Can the business card please have the following information on it.

Name: Warren Halbeck
Position: General Manager
Phone: 0472 915 348
Email: Warren.halbeck@tovrin.com.au
Address: 87 Marrow Ave, Pendlebay, QLD, 4023
Website: www.tovrin.com.au

Visually we'd like the card to be professional and simple.

Attached is our logo.

Our website is www.tovrin.com.au

Target Market(s)

Men aged 25-60

Contact Information for Business Card

As listed in project description

Font styles to use
Serif

Requirements
Must have
• Large logo on back of card

```html
<!DOCTYPE html>
<html lang="en">
<head>
<meta charset="utf-8">
<title>Tovrin – Business Card</title>
<link rel="stylesheet" href="https://fonts.googleapis.com/css2?family=Noto+Serif:wght@400;700&display=swap">
<style>
  :root {
    --bg: #474747;
    --card-dark: #181818;
    --brand-blue: #0a56a8;
    --accent-blue: #36a6d9;
    --text-light: #f2f2f2;
  }
  * { margin: 0; padding: 0; box-sizing: border-box; }
  html, body {
    width: 1200px; height: 801px; overflow: hidden;
    background: var(--bg);
    font-family: "Noto Serif", Georgia, serif;
  }
  .stage {
    position: relative; width: 1200px; height: 801px;
    display: flex; align-items: center; justify-content: center; gap: 40px;
  }
  .card {
    position: relative; width: 540px; height: 310px;
    border-radius: 16px; overflow: hidden;
  }
  .card--front {
    background: var(--card-dark);
    border-bottom: 5px solid var(--accent-blue);
  }
  .card--back { background: var(--accent-blue); }

  .wordmark {
    position: absolute; font-weight: 700; letter-spacing: 2px; line-height: 1;
  }
  .card--front .wordmark {
    left: 100px; top: 34px; font-size: 68px; color: var(--brand-blue);
  }
  .card--back .wordmark {
    left: 0; right: 0; top: 50%; transform: translateY(-50%);
    text-align: center; font-size: 104px; color: #ffffff;
  }

  .side-tab {
    position: absolute; left: 0; top: 186px; width: 40px; height: 30px;
    background: var(--accent-blue);
  }
  .divider {
    position: absolute; left: 58px; top: 200px; width: 420px; height: 1.5px;
    background: var(--accent-blue);
  }
  .person { position: absolute; left: 58px; top: 140px; }
  .person__name { font-size: 22px; font-weight: 700; color: var(--accent-blue); line-height: 1.1; }
  .person__role { font-size: 13px; color: var(--text-light); margin-top: 3px; }

  .address {
    position: absolute; right: 44px; top: 150px;
    font-size: 12px; line-height: 1.5; color: var(--text-light);
  }
  .contacts {
    position: absolute; left: 58px; top: 212px; list-style: none;
  }
  .contacts li {
    display: flex; align-items: center; gap: 9px;
    font-size: 13px; line-height: 23px; color: var(--text-light);
  }
  .contacts svg { width: 13px; height: 13px; fill: var(--accent-blue); flex: none; }
</style>
</head>
<body>
<main class="stage">
  <section class="card card--front" aria-label="Business card front">
    <div class="wordmark">Tovrin</div>
    <div class="person">
      <div class="person__name">Warren Halbeck</div>
      <div class="person__role">General Manager</div>
    </div>
    <div class="address">87 Marrow Ave,<br>Pendlebay, QLD, 4023</div>
    <div class="side-tab"></div>
    <div class="divider"></div>
    <ul class="contacts">
      <li>
        <svg viewBox="0 0 24 24" aria-hidden="true"><path d="M6.6 10.8a15 15 0 0 0 6.6 6.6l2.2-2.2a1 1 0 0 1 1-.25 11.4 11.4 0 0 0 3.6.57 1 1 0 0 1 1 1V20a1 1 0 0 1-1 1A17 17 0 0 1 3 4a1 1 0 0 1 1-1h3.5a1 1 0 0 1 1 1c0 1.25.2 2.45.57 3.6a1 1 0 0 1-.25 1z"/></svg>
        0472 915 348
      </li>
      <li>
        <svg viewBox="0 0 24 24" aria-hidden="true"><path d="M2 5h20v14H2zm2 2v.5l8 5 8-5V7zm0 2.8V17h16V9.8l-8 5z"/></svg>
        Warren.halbeck@tovrin.com.au
      </li>
      <li>
        <svg viewBox="0 0 24 24" aria-hidden="true"><path d="M12 2a10 10 0 1 0 0 20 10 10 0 0 0 0-20zm0 2c.9 0 2.2 1.9 2.8 5H9.2C9.8 5.9 11.1 4 12 4zM4.3 11h4.7c0 .7 0 1.4.1 2H4.3a8 8 0 0 1 0-2zm.6 4h4.4c.3 1.7.8 3.2 1.5 4.3A8 8 0 0 1 4.9 15zm4.3-6H4.9a8 8 0 0 1 5.9-4.3c-.7 1.1-1.2 2.6-1.5 4.3zm2.8 11c-.9 0-2.2-1.9-2.8-5h5.6c-.6 3.1-1.9 5-2.8 5zm3-7H9v-2h6zm-1.8 6.3c.7-1.1 1.2-2.6 1.5-4.3h4.4a8 8 0 0 1-5.9 4.3zM15 11h4.7a8 8 0 0 1 0 2H15zm-.3-2c-.3-1.7-.8-3.2-1.5-4.3A8 8 0 0 1 19.1 9z"/></svg>
        www.tovrin.com.au
      </li>
    </ul>
  </section>

  <section class="card card--back" aria-label="Business card back">
    <div class="wordmark">Tovrin</div>
  </section>
</main>
</body>
</html>
```